Flight school sign for building, banner, and bilboard

This sign is primarily for use on the side of our flight school building to draw attention for current and future flight school students. We offer airplane and helicopter flight training, ground school training and seminars, airplane and helicopter rentals, multi-engine training, and more. I would like a professional but exciting sign that can be used across a multitude of signage options such as banners, banner ads, billboard, and other mediums so that our sign is consistent and recognizable.

Contact Information for Business Card

The business card should match our company sign somewhat but not exactly. We want good and exciting imagery or wording and energizing/exciting colors.

```html
<!DOCTYPE html>
<html lang="en">
<head>
<meta charset="UTF-8">
<title>Northwind Aviation – Billboard</title>
<link rel="stylesheet" href="https://fonts.googleapis.com/css2?family=Montserrat:wght@300;500;700;800&display=swap">
<style>
  :root {
    --red: #e8232f;
    --navy: #2b3056;
    --white: #ffffff;
    --photo-sky: #eef0f3;
    --photo-body: #d7dadf;
    --photo-tail: #c9262f;
    --photo-shadow: #dcdde0;
  }
  * { margin: 0; padding: 0; box-sizing: border-box; }
  html, body {
    width: 1200px;
    height: 785px;
    overflow: hidden;
    background: var(--white);
  }
  .billboard {
    position: relative;
    width: 1200px;
    height: 785px;
    background: var(--white);
    font-family: "Montserrat", sans-serif;
    overflow: hidden;
  }
  .bands {
    position: absolute;
    inset: 0;
    width: 1200px;
    height: 785px;
  }
  .brand {
    position: absolute;
    left: 110px;
    top: 150px;
    width: 440px;
    text-align: center;
  }
  .brand-name {
    display: inline-flex;
    align-items: center;
    gap: 10px;
    white-space: nowrap;
    font-weight: 500;
    font-size: 31px;
    letter-spacing: 0.5px;
    color: var(--navy);
    line-height: 1;
  }
  .brand-mark {
    width: 16px;
    height: 16px;
    border-radius: 50%;
    background: var(--red);
    flex: none;
  }
  .brand-tagline {
    margin-top: 9px;
    font-weight: 700;
    font-size: 10px;
    letter-spacing: 1.6px;
    color: var(--red);
    text-transform: uppercase;
    white-space: nowrap;
  }
  .headline {
    position: absolute;
    left: 120px;
    top: 272px;
    line-height: 1.04;
    text-transform: uppercase;
    white-space: nowrap;
  }
  .headline-lead {
    display: block;
    font-weight: 300;
    font-size: 72px;
    color: var(--navy);
  }
  .headline-strong {
    display: block;
    font-weight: 700;
    font-size: 72px;
    color: var(--navy);
  }
  .headline-accent {
    display: block;
    font-weight: 800;
    font-size: 72px;
    color: var(--red);
  }
  .phone {
    position: absolute;
    left: 40px;
    top: 586px;
    font-weight: 800;
    font-size: 52px;
    color: var(--white);
    letter-spacing: 0.5px;
    white-space: nowrap;
  }
  .website {
    position: absolute;
    left: 40px;
    top: 712px;
    font-weight: 500;
    font-size: 30px;
    color: var(--white);
    white-space: nowrap;
  }
  .aircraft-photo {
    position: absolute;
    left: 600px;
    top: 110px;
    width: 575px;
    height: 450px;
    border-radius: 4px;
    background:
      linear-gradient(180deg, var(--photo-sky) 0%, var(--photo-body) 55%, var(--photo-sky) 80%, var(--photo-shadow) 100%);
  }
</style>
</head>
<body>
  <main class="billboard">
    <svg class="bands" viewBox="0 0 1200 785" aria-hidden="true">
      <polygon points="0,0 95,0 80,22 0,22" fill="var(--red)"/>
      <polygon points="0,22 80,22 66,46 0,46" fill="var(--navy)"/>
      <polygon points="880,0 1200,0 1200,24 868,24" fill="var(--red)"/>
      <polygon points="945,24 1200,24 1200,54 935,54" fill="var(--navy)"/>
      <polygon points="0,565 610,565 640,665 0,665" fill="var(--red)"/>
      <polygon points="0,682 470,682 500,785 0,785" fill="var(--navy)"/>
    </svg>

    <header class="brand">
      <div class="brand-name"><span class="brand-mark"></span>NORTHWIND AVIATION</div>
      <p class="brand-tagline">Small step today, giant leap tomorrow</p>
    </header>

    <h1 class="headline">
      <span class="headline-lead">Are you</span>
      <span class="headline-strong">Ready to</span>
      <span class="headline-accent">Take off</span>
    </h1>

    <div class="aircraft-photo" role="img" aria-label="Photo of a white passenger jet with a red tail, seen head-on with landing gear down and a soft shadow beneath"></div>

    <p class="phone">(+1) 555 010 2030</p>
    <p class="website">www.northwindflight.com</p>
  </main>
</body>
</html>
```